Wealth Education Business Needs Sharp Business Card Design

We need a business card design for a recently launched investor education business called Harbor Crest.

The final design should promote security, empowerment, self improvement and financial gain. The card will ideally promote the stature of the business.

For more information and colours please visit harborcrest.com.au

Target Market(s)

Corporate executives and high net worth individuals

Industry/Entity Type

Education

Contact Information for Business Card

```html
<!DOCTYPE html>
<html lang="en">
<head>
<meta charset="utf-8">
<title>Harbor Crest – Business Card</title>
<link href="https://fonts.googleapis.com/css2?family=Oswald:wght@300&family=Lato:ital,wght@0,400;0,700;1,400&display=swap" rel="stylesheet">
<style>
  :root {
    --backdrop: #3b3b3c;
    --navy: #1f2a3d;
    --paper: #ffffff;
    --ink: #2e2b2c;
    --swoosh: #4a4a4c;
    --text-light: #ffffff;
  }
  * { box-sizing: border-box; margin: 0; padding: 0; }
  html, body {
    width: 1200px; height: 960px; overflow: hidden;
    background: var(--backdrop);
    font-family: "Lato", Arial, sans-serif;
  }
  .card {
    position: absolute;
    left: 270px; width: 645px; height: 369px;
    overflow: hidden;
    box-shadow: 0 6px 14px rgba(0,0,0,0.45);
  }
  .card--front { top: 83px; background: var(--navy); }
  .card--back { top: 507px; background: var(--paper); }

  .wordmark {
    position: absolute;
    font-family: "Oswald", "Arial Narrow", sans-serif;
    font-weight: 300;
    font-size: 30px;
    letter-spacing: 5px;
    white-space: nowrap;
    line-height: 1;
  }
  .card--front .wordmark { right: 58px; top: 84px; color: var(--text-light); }
  .card--back .wordmark { left: 59px; top: 72px; color: var(--ink); }

  .front-url {
    position: absolute; right: 117px; bottom: 32px;
    color: var(--text-light); font-size: 14.5px;
  }

  .back-band { position: absolute; inset: 0; }

  .address, .contact-list, .person {
    position: absolute; color: var(--text-light);
  }
  .address { left: 59px; top: 207px; font-size: 15px; line-height: 19px; }
  .contact-list { left: 57px; top: 264px; list-style: none; font-size: 15px; }
  .contact-list li { display: flex; align-items: center; height: 20.7px; }
  .contact-list svg { width: 16px; height: 16px; margin-right: 13px; flex: none; }
  .person { right: 86px; top: 296px; text-align: right; }
  .person__name { font-weight: 700; font-size: 18px; line-height: 22px; }
  .person__role { font-style: italic; font-size: 14px; line-height: 16px; }
</style>
</head>
<body>

<section class="card card--front" aria-label="Card front">
  <div class="wordmark">HARBOR CREST</div>
  <div class="front-url">www.harborcrest.com.au</div>
</section>

<section class="card card--back" aria-label="Card back">
  <div class="wordmark">HARBOR CREST</div>

  <svg class="back-band" viewBox="0 0 645 369" width="645" height="369" aria-hidden="true">
    <path d="M0,150 Q330,128 560,232 Q330,140 0,170 Z" fill="var(--swoosh)"/>
    <path d="M0,181 Q340,150 645,290 L645,369 L0,369 Z" fill="var(--navy)"/>
  </svg>

  <p class="address">Level 4, 27 Harbour Row<br>Docklands VIC 3008</p>

  <ul class="contact-list">
    <li>
      <svg viewBox="0 0 16 16"><path d="M2 6 Q8 1 14 6 L12 8 L10 6.5 L6 6.5 L4 8 Z M4 9 L12 9 L13 14 L3 14 Z" fill="#fff"/></svg>
      1300.555.018
    </li>
    <li>
      <svg viewBox="0 0 16 16"><rect x="4.5" y="1" width="7" height="14" rx="1.5" fill="none" stroke="#fff" stroke-width="1.4"/><circle cx="8" cy="12.5" r="0.9" fill="#fff"/></svg>
      0000.000.000
    </li>
    <li>
      <svg viewBox="0 0 16 16"><rect x="1.5" y="3.5" width="13" height="9" fill="none" stroke="#fff" stroke-width="1.4"/><path d="M1.5 3.5 L8 9 L14.5 3.5" fill="none" stroke="#fff" stroke-width="1.4"/></svg>
      support@harborcrest.com.au
    </li>
    <li>
      <svg viewBox="0 0 16 16" fill="none" stroke="#fff" stroke-width="1.2"><circle cx="8" cy="8" r="6.5"/><ellipse cx="8" cy="8" rx="3" ry="6.5"/><path d="M1.5 8 H14.5 M2.5 4.8 H13.5 M2.5 11.2 H13.5"/></svg>
      www.harborcrest.com.au
    </li>
  </ul>

  <div class="person">
    <div class="person__name">Marcus Hale</div>
    <div class="person__role">Founder &amp; CEO</div>
  </div>
</section>

</body>
</html>
```